Payment company requires web design

We need a web design for a new company based in Singapore.

The company focuses on providing 2 key products: 1) an alternative payment option (i.e. like quib or trelloquin options) on the traditional checkout process 2) a replacement/outsource of a merchants payment page. Key in the UX flow is a end customer dashboard that manages all payments.

We look to provide a simple, fluid and easy to use payment process. The dashboard is minimalistic that allows easy navigation, review of transactions and all available options through gamification.

The final design should communicate ease of use, flexibility and transparency.

Target Market(s)

The value is for the merchant - retail/travel/insurance companies. However its the merchant's end customers that are the target and who the UX is built for.

Industry/Entity Type

It Company

Logo Text

zelnar

Number of Pages Required

5+ page

Colors
ec1f27

Requirements
Must have
• 7 pages mimicking UX flow
• payment page * 2 - 1) alternative payment type 2) outsource of merchants payment page to our business
• our landing page
• end customer verification page
• end customer registration
• customer dashboard
• UX flow in attached file
Nice to have
• open to ideas
• have asked for the logo to be added
• logo to have the colour red (chinese for prosperity)
• the company is all about flexibility, transparency in personal finance management with the option of instalment payments

```html
<!DOCTYPE html>
<html lang="en">
<head>
<meta charset="utf-8">
<title>Zelnar — Payment Processing</title>
<link href="https://fonts.googleapis.com/css2?family=Open+Sans:wght@400;600;700&family=Roboto:wght@400;500;700&display=swap" rel="stylesheet">
<style>
:root{
  --red:#ec1f27;
  --ink:#2b2b2b;
  --body:#666;
  --muted:#777;
  --light:#f4f4f4;
  --white:#fff;
  --footer:#262626;
  --footer-line:#3a3a3a;
}
*{margin:0;padding:0;box-sizing:border-box}
html,body{width:711px;height:1200px;overflow:hidden;background:var(--white)}
body{font-family:"Roboto",sans-serif;color:var(--ink)}
.page{position:relative;width:711px;height:1200px;overflow:hidden}
.abs{position:absolute}
.heading{font-family:"Open Sans",sans-serif;font-weight:600;color:var(--ink)}
.btn{position:absolute;background:var(--red);color:var(--white);font-family:"Open Sans",sans-serif;font-weight:700;display:flex;align-items:center;justify-content:center;text-transform:uppercase;border-radius:2px}

/* header */
.topbar{left:0;top:0;width:711px;height:2px;background:var(--red)}
.header{left:0;top:2px;width:711px;height:64px;background:var(--white)}
.logo{left:45px;top:16px;font-family:"Open Sans",sans-serif;font-weight:600;font-size:24px;color:var(--red);letter-spacing:.5px}
.nav a{position:absolute;top:29px;font-size:9px;color:#333;text-decoration:none;text-transform:uppercase;letter-spacing:.2px}
.nav a.active{color:var(--red)}

/* hero */
.hero{left:0;top:66px;width:711px;height:287px;background:linear-gradient(120deg,#3c4450 0%,#5b6470 35%,#7a7f86 60%,#4f4a48 100%)}
.hero-shade{left:0;top:66px;width:711px;height:287px;background:rgba(20,24,30,.25)}
.hero-title{left:0;width:711px;top:150px;text-align:center;font-family:"Open Sans",sans-serif;font-weight:600;font-size:20px;line-height:28px;color:var(--white)}
.hero-text{left:0;width:711px;top:214px;text-align:center;font-size:9.6px;line-height:14px;color:#f0f0f0}
.hero-btn{left:298px;top:258px;width:116px;height:26px;font-size:9px}
.arrow{top:190px}

/* welcome */
.welcome-title{left:45px;top:395px;font-size:15px}
.welcome-text{left:45px;top:431px;width:405px;font-size:7.3px;line-height:16.3px;color:var(--body)}
.btn-sm{font-size:7px;height:21px}
.how-title{left:483px;top:395px;font-size:15px}
.how-item .name{position:absolute;left:517px;font-family:"Open Sans",sans-serif;font-weight:600;font-size:10px;color:var(--red)}
.how-item .desc{position:absolute;left:517px;font-size:7.3px;color:var(--muted)}

/* reasons */
.reasons{left:0;top:560px;width:711px;height:347px;background:var(--light)}
.reasons-title{left:44px;top:601px;font-size:14px}
.card{position:absolute;top:640px;width:186px;height:230px;background:var(--white);border:1px solid #e4e4e4}
.card .photo{width:100%;height:106px}
.card .title{position:absolute;left:14px;top:124px;font-family:"Open Sans",sans-serif;font-weight:600;font-size:9.6px;color:var(--red)}
.card .text{position:absolute;left:14px;top:145px;width:160px;font-size:7.3px;line-height:13px;color:var(--muted)}
.card .btn{left:15px;top:195px;width:64px;height:20px;font-size:6.8px}

/* cta */
.cta-title{left:0;top:943px;width:711px;text-align:center;font-family:"Open Sans",sans-serif;font-weight:400;font-size:16.5px;line-height:24px;color:#333}
.cta-btn{left:304px;top:1002px;width:98px;height:25px;font-size:7.3px}

/* footer */
.footer{left:0;top:1064px;width:711px;height:136px;background:linear-gradient(#2c2c2c,var(--footer))}
.footer-logo{left:47px;top:1094px;font-family:"Open Sans",sans-serif;font-weight:600;font-size:21px;color:var(--white);letter-spacing:.5px}
.footer-icon{position:absolute;top:1098px}
.footer-text{position:absolute;font-size:7.3px;line-height:13px;color:#e8e8e8}
.footer-text strong{font-size:10px;font-weight:500;color:var(--white)}
.footer-line{left:0;top:1149px;width:711px;height:1px;background:var(--footer-line)}
.copyright{left:0;width:711px;top:1170px;text-align:center;font-size:7.3px;color:#ddd}
</style>
</head>
<body>
<div class="page">

  <div class="abs topbar"></div>
  <header class="abs header"></header>
  <div class="abs logo">ZELNAR</div>
  <nav class="nav">
    <a class="active" style="left:303px">Home</a>
    <a style="left:354px">About Us</a>
    <a style="left:418px">FAQ</a>
    <a style="left:463px">Customer</a>
    <a style="left:544px">Service</a>
    <a style="left:612px">Contact Us</a>
  </nav>

  <section class="abs hero" role="img" aria-label="Photo of hands typing on a laptop while holding a payment card"></section>
  <div class="abs hero-shade"></div>
  <h1 class="abs hero-title">WE ARE PAYMENT<br>PROCESSING COMPANY</h1>
  <p class="abs hero-text">Nam finibus dapibus dolor, vel ornare tortor elementum quis. Suspendisse<br>bibendum mi ac venenatis tincidunt.</p>
  <div class="btn hero-btn">Register Here</div>
  <svg class="abs arrow" style="left:45px" width="18" height="30" viewBox="0 0 18 30"><polyline points="15,2 3,15 15,28" fill="none" stroke="#fff" stroke-width="1.4"/></svg>
  <svg class="abs arrow" style="left:650px" width="18" height="30" viewBox="0 0 18 30"><polyline points="3,2 15,15 3,28" fill="none" stroke="#fff" stroke-width="1.4"/></svg>

  <h2 class="abs heading welcome-title">WELCOME TO OUR SITE</h2>
  <p class="abs welcome-text">Phasellus tincidunt felis enim, et facilisis orci dictum a. Suspendisse hendrerit massa nec tellus hendrerit bibendum. Duis et molestie eros. Aenean turpis metus, fringilla in maximus vitae, rutrum nec nulla. Pellentesque gravida, nibh condimentum pulvinar suscipit, diam ipsum sollicitudin felis, eu consectetur quam nunc ut ante. Phasellus tincidunt felis enim, et facilisis orci dictum a. Suspendisse hendrerit massa ne.</p>
  <div class="btn btn-sm" style="left:46px;top:505px;width:65px">Read More</div>

  <h2 class="abs heading how-title">HOW IT WORK</h2>
  <div class="how-item">
    <svg class="abs" style="left:484px;top:433px" width="17" height="17" viewBox="0 0 17 17"><circle cx="8.5" cy="5" r="4" fill="var(--red)"/><path d="M1 17c0-5 3.5-7 7.5-7s7.5 2 7.5 7z" fill="var(--red)"/></svg>
    <span class="name" style="top:430px">CUSTOMER</span>
    <span class="desc" style="top:445px">In maximus vitae, rutrum nec nulla</span>
  </div>
  <div class="how-item">
    <svg class="abs" style="left:484px;top:475px" width="22" height="17" viewBox="0 0 22 17"><rect x="1" y="1" width="20" height="15" fill="none" stroke="var(--red)" stroke-width="1.8"/><text x="11" y="13" text-anchor="middle" font-family="Open Sans,sans-serif" font-weight="700" font-size="10" fill="var(--red)">CC</text></svg>
    <span class="name" style="top:471px">CARD NETWORK</span>
    <span class="desc" style="top:490px">sedu eu consectetur quam nunc ut ante</span>
  </div>
  <div class="how-item">
    <svg class="abs" style="left:484px;top:510px" width="20" height="18" viewBox="0 0 20 18"><path d="M2 17c0-7 4-10 10-10V3l7 6-7 6v-4c-4 0-7 1.5-10 6z" fill="var(--red)"/></svg>
    <span class="name" style="top:508px">EASY CHECKOUT</span>
    <span class="desc" style="top:522px">In maximus vitae, rutrum nec nulla</span>
  </div>

  <section class="abs reasons"></section>
  <h2 class="abs heading reasons-title">REASON TO USE ZELNAR</h2>

  <article class="card" style="left:45px">
    <div class="photo" role="img" aria-label="Photo of a phone tapped on a card terminal" style="background:linear-gradient(135deg,#5a3a40,#9a7a78 55%,#d8d0cc)"></div>
    <h3 class="title">MORBI AT TELLUS SIT AMET</h3>
    <p class="text">Diam ipsum sollicitudin felis, eu consectetur quam nunc ut ante. Phasellus tincidunt felis enim, et facilisis orci dictum</p>
    <div class="btn">Read More</div>
  </article>
  <article class="card" style="left:262px">
    <div class="photo" role="img" aria-label="Photo of hands using a tablet while holding a card" style="background:linear-gradient(135deg,#e6e8ec,#a9b5c6 50%,#c9c4bd)"></div>
    <h3 class="title" style="left:17px">AENEAN MATTIS EUIS</h3>
    <p class="text">Diam ipsum sollicitudin felis, eu consectetur quam nunc ut ante. Phasellus tincidunt felis enim, et facilisis orci dictum</p>
    <div class="btn">Read More</div>
  </article>
  <article class="card" style="left:479px">
    <div class="photo" role="img" aria-label="Photo of a card inserted into a handheld payment terminal" style="background:linear-gradient(135deg,#4d5c7a,#8a94a8 50%,#3a3c44)"></div>
    <h3 class="title">MORBI AT TELLUS SIT AMET</h3>
    <p class="text">Diam ipsum sollicitudin felis, eu consectetur quam nunc ut ante. Phasellus tincidunt felis enim, et facilisis orci dictum</p>
    <div class="btn">Read More</div>
  </article>

  <h2 class="abs cta-title">Ready to get started? Get in touch,<br>or create an account</h2>
  <div class="btn cta-btn">Create Account »</div>

  <footer class="abs footer"></footer>
  <div class="abs footer-logo">ZELNAR</div>

  <svg class="footer-icon" style="left:202px" width="21" height="21" viewBox="0 0 21 21"><circle cx="10.5" cy="10.5" r="9.8" fill="none" stroke="#ddd" stroke-width="1"/><path d="M10.5 5.5a3.2 3.2 0 0 0-3.2 3.2c0 2.4 3.2 6 3.2 6s3.2-3.6 3.2-6a3.2 3.2 0 0 0-3.2-3.2z" fill="#fff"/><circle cx="10.5" cy="8.7" r="1.1" fill="#2a2a2a"/></svg>
  <p class="footer-text" style="left:231px;top:1096px">CONTACT :&nbsp; Zelnar Pte Lindenweg<br>12 4010 Marlau</p>

  <svg class="footer-icon" style="left:432px" width="21" height="21" viewBox="0 0 21 21"><circle cx="10.5" cy="10.5" r="9.8" fill="none" stroke="#ddd" stroke-width="1"/><path d="M7.2 5.8l1.6-.4 1.1 2.3-1 .8c.5 1.2 1.4 2.1 2.6 2.6l.8-1 2.3 1.1-.4 1.6c-3.6.3-7.3-3.4-7-7z" fill="#fff"/></svg>
  <p class="footer-text" style="left:461px;top:1096px">Telephone:<br><strong>1800 376 9021</strong></p>

  <svg class="footer-icon" style="left:571px" width="21" height="21" viewBox="0 0 21 21"><circle cx="10.5" cy="10.5" r="9.8" fill="none" stroke="#ddd" stroke-width="1"/><rect x="6" y="7.3" width="9" height="6.4" rx=".8" fill="none" stroke="#fff" stroke-width="1.1"/><polyline points="6.3,7.8 10.5,11 14.7,7.8" fill="none" stroke="#fff" stroke-width="1.1"/></svg>
  <p class="footer-text" style="left:600px;top:1096px">Email:<br>hello@zelnar.example</p>

  <div class="abs footer-line"></div>
  <p class="abs copyright">Copyright ©,&nbsp; Zelnar.&nbsp; All Rights Reserved.</p>
</div>
</body>
</html>
```